Business Card for premium dental clinic

We are a premium dental clinic based in Brasov, Romania with more than 15 year on the market, providing quality dental treatment made by a team of more specialized dentists, working with modern equipment as a solution to beautiful and healthy teeth.

Our current logo for the clinic use 2 square with colors black and gold - dr Ternisu - studio, using family fonts Bodoni, Myriad Pro and Segoe Print.
Depending on the printing we used some gold CMYK background or gold foil picture background or a gold gradient.
We want a business card:
- eye catching business card
- distinguished business card
- premium design
- to keep the color scheme of black and gold
- to attract the customers to spent time reading the information
- modern concept

```html
<!DOCTYPE html>
<html lang="en">
<head>
<meta charset="utf-8">
<title>Lumina Dental Clinic – Business Card</title>
<link href="https://fonts.googleapis.com/css2?family=Montserrat:wght@300;400&family=Oswald:wght@300;400&display=swap" rel="stylesheet">
<style>
  :root {
    --page: #e6e7e8;
    --card-black: #050707;
    --gold-bright: #f4ea6a;
    --gold-warm: #fad04a;
    --gold-bronze: #d9a13e;
    --address-gold: #f2d43c;
    --text-white: #ffffff;
  }
  * { margin: 0; padding: 0; box-sizing: border-box; }
  html, body { width: 1200px; height: 1200px; overflow: hidden; background: var(--page); }
  .sheet { position: relative; width: 1200px; height: 1200px; }
  .card {
    position: absolute; top: 453px; width: 516px; height: 294px;
    background: var(--card-black);
    box-shadow: 12px 10px 8px rgba(0,0,0,.38);
    overflow: hidden;
  }
  .card--front { left: 50px; }
  .card--back { left: 632px; }

  .gold-field {
    position: absolute; top: 0; bottom: 0; width: 140px;
    background: linear-gradient(160deg, var(--gold-bronze) 0%, var(--gold-bright) 50%, var(--gold-warm) 100%);
  }
  .card--front .gold-field { right: 0; }
  .card--back .gold-field { left: 0; }

  .doctor-name {
    position: absolute; left: 54px; top: 40px; width: 114px; height: 40px;
    display: flex; align-items: center; justify-content: center;
    font-family: "Oswald", sans-serif; font-weight: 300;
    color: var(--text-white); font-size: 35px; letter-spacing: .5px;
  }
  .contacts { position: absolute; left: 44px; top: 124px; list-style: none; }
  .contacts__item {
    display: flex; align-items: center; height: 21.6px;
    font-family: "Montserrat", sans-serif; font-weight: 300;
    font-size: 14.5px; color: var(--text-white); letter-spacing: .2px;
  }
  .contacts__icon { width: 14px; height: 14px; margin-right: 10px; flex: none; }
  .address {
    position: absolute; left: 44px; top: 238px;
    font-family: "Montserrat", sans-serif; font-weight: 300;
    font-size: 14.5px; line-height: 16px; color: var(--address-gold);
  }

  .clinic-name {
    position: absolute; left: 210px; top: 64px; width: 200px; text-align: center;
    font-family: "Oswald", sans-serif; font-weight: 300;
    font-size: 50px; color: var(--text-white); letter-spacing: 1px;
  }
  .clinic-tagline {
    position: absolute; left: 294px; top: 180px;
    font-family: "Oswald", sans-serif; font-weight: 300;
    font-size: 38px; color: var(--text-white);
  }
</style>
</head>
<body>
<div class="sheet">

  <section class="card card--front">
    <div class="gold-field" role="img" aria-label="Gold metallic decorative area"></div>

    <div class="doctor-name">dr.ternisu</div>

    <ul class="contacts">
      <li class="contacts__item">
        <svg class="contacts__icon" viewBox="0 0 16 16" fill="none" stroke="#f2d43c" stroke-width="1.2"><path d="M3 2 L6 2 L7 5 L5 6.5 C6 9 7 10 9.5 11 L11 9 L14 10 L14 13 C9 14 2 7 3 2 Z"/><path d="M10 2 A4 4 0 0 1 14 6"/></svg>
        +00 000 417 5200
      </li>
      <li class="contacts__item">
        <svg class="contacts__icon" viewBox="0 0 16 16" fill="none" stroke="#f2d43c" stroke-width="1.4"><rect x="5" y="2" width="6" height="12" rx="1"/><path d="M7.5 12h1"/></svg>
        +00 000 417 5211
      </li>
      <li class="contacts__item">
        <svg class="contacts__icon" viewBox="0 0 16 16" fill="none" stroke="#f2d43c" stroke-width="1.2"><rect x="1.5" y="4" width="13" height="8.5"/><path d="M1.5 4 L8 9 L14.5 4"/></svg>
        info@luminadental.com
      </li>
      <li class="contacts__item">
        <svg class="contacts__icon" viewBox="0 0 16 16" fill="none" stroke="#f2d43c" stroke-width="1.1"><circle cx="8" cy="8" r="6.5"/><ellipse cx="8" cy="8" rx="3" ry="6.5"/><path d="M1.5 8h13M2.5 5h11M2.5 11h11"/></svg>
        www.luminadental.com
      </li>
    </ul>

    <p class="address">18 Aurora Lane<br>london NSW 2100</p>
  </section>

  <section class="card card--back">
    <div class="gold-field" role="img" aria-label="Gold metallic decorative area"></div>

    <div class="clinic-name">lumina</div>
    <div class="clinic-tagline">dental clinic</div>
  </section>

</div>
</body>
</html>
```